Brantor Works Business Card

Modern and Professional Business Card for a Med size construction/development company.

See the samples below for the design I like … but I need ideas for incorporating the red company logo while still keeping the clean look of the card samples that are attached.

Logo and tag line on the back … info on the front.

Tagline: Built Right from the Footings Up

Target Market(s)

Med-Large General Contractors

Contact Information for Business Card

Brantor Works Limited
42 Fenwick Avenue
Mt. Pearl, NL
A1N 4R9

t: 709-555-0147
f: 709-555-0182
w: www.brantorworks-example.com

Font styles to use
Sans Serif

Colors
fbee3e

Requirements
Must have
• I like the black and yellow designs of the attached samples …. but I'm not sure how to incorporate the red Brantor Works logo into that design??
Nice to have
• Construction safety strips

```html
<!DOCTYPE html>
<html lang="en">
<head>
<meta charset="utf-8">
<title>Brantor Works Limited — Business Card</title>
<link rel="stylesheet" href="https://fonts.googleapis.com/css2?family=Montserrat:wght@700&family=Questrial&display=swap">
<style>
  :root {
    --backdrop: #3a3d42;
    --card: #060709;
    --yellow: #f7ec3a;
    --red: #ed1c24;
    --white: #ffffff;
    --shadow: rgba(0, 0, 0, 0.45);
  }
  * { margin: 0; padding: 0; box-sizing: border-box; }
  html, body {
    width: 1200px;
    height: 1000px;
    overflow: hidden;
    background: var(--backdrop);
  }
  .canvas {
    position: relative;
    width: 1200px;
    height: 1000px;
  }
  .card {
    position: absolute;
    left: 250px;
    width: 700px;
    height: 400px;
    background: var(--card);
    border-radius: 22px;
    box-shadow: 0 14px 34px var(--shadow);
    font-family: "Questrial", sans-serif;
    color: var(--white);
  }
  .card--back { top: 60px; }
  .card--front { top: 540px; }

  /* Back side: brand name + tagline */
  .brand {
    position: absolute;
    display: flex;
    align-items: center;
    gap: 14px;
  }
  .brand__mark {
    width: 34px;
    height: 34px;
    border-radius: 4px;
  }
  .brand__name {
    font-family: "Montserrat", sans-serif;
    font-weight: 700;
    line-height: 1;
    white-space: nowrap;
  }
  .card--back .brand {
    left: 50%;
    top: 140px;
    transform: translateX(-50%);
  }
  .card--back .brand__mark { background: var(--red); }
  .card--back .brand__name { font-size: 34px; color: var(--white); }
  .tagline {
    position: absolute;
    left: 0;
    right: 0;
    top: 235px;
    text-align: center;
    font-size: 20px;
    letter-spacing: 0.5px;
  }

  /* Front side: contact details */
  .company-title {
    position: absolute;
    left: 48px;
    top: 40px;
    font-family: "Montserrat", sans-serif;
    font-weight: 700;
    font-size: 26px;
    line-height: 1.2;
    color: var(--yellow);
  }
  .company-title__rule {
    display: block;
    width: 96px;
    height: 2px;
    margin-top: 8px;
    background: var(--yellow);
  }
  .card--front .brand {
    right: 48px;
    top: 146px;
  }
  .card--front .brand__mark { background: var(--yellow); width: 30px; height: 30px; }
  .card--front .brand__name { font-size: 28px; color: var(--yellow); }

  .contact-list {
    position: absolute;
    left: 48px;
    top: 240px;
    list-style: none;
    font-size: 20px;
    line-height: 1.5;
  }
  .contact-list__item {
    display: flex;
    align-items: center;
    gap: 12px;
  }
  .contact-list__icon {
    width: 17px;
    height: 17px;
    flex: none;
    fill: var(--yellow);
  }
  .contact-list .highlight { color: var(--yellow); }

  .address {
    position: absolute;
    right: 48px;
    bottom: 36px;
    text-align right;
    text-align: right;
    font-style: normal;
    font-size: 22px;
    line-height: 1.3;
  }
</style>
</head>
<body>
<main class="canvas">

  <section class="card card--back" aria-label="Card back">
    <div class="brand">
      <span class="brand__mark"></span>
      <span class="brand__name">Brantor Works Limited</span>
    </div>
    <p class="tagline">Built Right from the Footings Up</p>
  </section>

  <section class="card card--front" aria-label="Card front">
    <h1 class="company-title">
      Brantor Works<br>Limited
      <span class="company-title__rule"></span>
    </h1>

    <div class="brand">
      <span class="brand__mark"></span>
      <span class="brand__name">Brantor Works</span>
    </div>

    <ul class="contact-list">
      <li class="contact-list__item">
        <svg class="contact-list__icon" viewBox="0 0 24 24" aria-hidden="true"><path d="M6.6 10.8a15.1 15.1 0 0 0 6.6 6.6l2.2-2.2c.3-.3.7-.4 1-.2 1.1.4 2.3.6 3.6.6.6 0 1 .4 1 1V20c0 .6-.4 1-1 1A17 17 0 0 1 3 4c0-.6.4-1 1-1h3.5c.6 0 1 .4 1 1 0 1.3.2 2.5.6 3.6.1.3 0 .7-.2 1z"/></svg>
        <span>709-555-0147</span>
      </li>
      <li class="contact-list__item">
        <svg class="contact-list__icon" viewBox="0 0 24 24" aria-hidden="true"><path d="M6 2h12v5H6zM4 8h16a2 2 0 0 1 2 2v7h-4v5H6v-5H2v-7a2 2 0 0 1 2-2zm4 8v4h8v-4z"/></svg>
        <span>709-555-0182</span>
      </li>
      <li class="contact-list__item">
        <svg class="contact-list__icon" viewBox="0 0 24 24" aria-hidden="true"><path d="M2 5h20v14H2zm2 2v.5l8 5 8-5V7zm0 2.8V17h16V9.8l-8 5z"/></svg>
        <span>info@brantorworks-example.com</span>
      </li>
      <li class="contact-list__item">
        <svg class="contact-list__icon" viewBox="0 0 24 24" aria-hidden="true"><path d="M12 2a10 10 0 1 0 0 20 10 10 0 0 0 0-20zm0 2c1 0 2.3 2 2.8 5H9.2C9.7 6 11 4 12 4zM4.3 11h4.8a18 18 0 0 0 0 2H4.3a8 8 0 0 1 0-2zm10.6 0h4.8a8 8 0 0 1 0 2h-4.8a18 18 0 0 0 0-2zM9.2 15h5.6c-.5 3-1.8 5-2.8 5s-2.3-2-2.8-5z"/></svg>
        <span>www.<span class="highlight">brantorworks-example</span>.com</span>
      </li>
    </ul>

    <address class="address">
      42 Fenwick Avenue<br>
      Harbour Vale, NL B2K 7T3
    </address>
  </section>

</main>
</body>
</html>
```